Website for Torvel Capital - investment banking firm

We have a corporate identity (thanks to Ravinka/31842) and want to extend that into a website design.  See the attached zipped files.
We have software folks in-house to do the coding.
See the attached Project Brief & Notes for more details.  Don't worry about the actual text - lorem ipsum will be fine.
The server will be Apache.
Thank you!
Desmond

Industry/Entity Type
Investment

```html
<!DOCTYPE html>
<html lang="en">
<head>
<meta charset="utf-8">
<title>Torvel Capital – Investment Banking</title>
<link rel="stylesheet" href="https://fonts.googleapis.com/css2?family=Figtree:wght@400;500;600&family=Cinzel:wght@500&display=swap">
<style>
  :root {
    --page-bg: #d8d8d8;
    --sheet: #ffffff;
    --brand-blue: #1b4a8c;
    --link-blue: #1f4f91;
    --text: #555555;
    --text-dark: #3e3e3e;
    --rule: #d9d9d9;
    --muted: #a7a7a7;
  }
  * { box-sizing: border-box; margin: 0; padding: 0; }
  html, body { width: 1200px; height: 887px; overflow: hidden; }
  body {
    background: var(--page-bg);
    font-family: "Figtree", sans-serif;
    color: var(--text);
    position: relative;
  }
  .sheet {
    position: absolute; left: 122px; top: 0; width: 960px; height: 887px;
    background: var(--sheet);
    box-shadow: 0 0 6px rgba(0,0,0,.12);
  }
  .abs { position: absolute; }

  .brand { left: 13px; top: 30px; display: flex; align-items: center; gap: 12px; }
  .brand-mark { width: 44px; height: 44px; background: var(--brand-blue); }
  .brand-name { font-size: 34px; font-weight: 600; color: var(--brand-blue); letter-spacing: .5px; }

  .account { right: 19px; top: 52px; display: flex; gap: 22px; font-size: 15px; letter-spacing: .8px; color: var(--text-dark); }
  .account span.sep { color: var(--text-dark); }

  .main-nav {
    left: 11px; top: 115px; width: 937px; height: 38px; background: var(--brand-blue);
    display: flex; align-items: center; padding-left: 27px;
  }
  .main-nav a { color: #fff; text-decoration: none; font-size: 14px; font-weight: 500; }
  .main-nav .sep { color: #fff; opacity: .8; margin: 0 20px; font-size: 12px; }
  .search { position: absolute; right: 14px; top: 7px; display: flex; }
  .search input { width: 139px; height: 23px; border: 0; font: 12px "Figtree", sans-serif; padding-left: 8px; color: #888; }
  .search button { width: 24px; height: 23px; border: 0; background: #9a9a9a; display: flex; align-items: center; justify-content: center; }

  .hero-art {
    left: 11px; top: 170px; width: 684px; height: 270px;
    background: linear-gradient(100deg, #f1f6f9 0%, #d8e7f0 30%, #8fb3cc 55%, #4f7d9f 80%, #6f9ab8 100%);
  }
  .hero-title { left: 28px; top: 195px; font-family: "Cinzel", serif; font-size: 25px; color: #2c3340; letter-spacing: 1px; }
  .hero-lede { left: 27px; top: 235px; width: 330px; font-size: 16px; line-height: 25px; color: var(--text); }
  .more { font-size: 13px; font-weight: 600; letter-spacing: .6px; color: var(--link-blue); text-decoration: underline; text-underline-offset: 3px; }
  .hero-dots { left: 29px; top: 348px; display: flex; gap: 5px; }
  .hero-dots i { width: 12px; height: 11px; background: var(--muted); }
  .hero-dots i.on { background: var(--brand-blue); }

  .services { left: 711px; top: 178px; width: 240px; }
  .services h2 { font-size: 19px; font-weight: 400; color: var(--text-dark); margin-bottom: 22px; }
  .services li { list-style: none; font-size: 14px; line-height: 31px; display: flex; align-items: center; gap: 9px; padding-left: 2px; }
  .services li::before { content: ""; border-left: 8px solid var(--brand-blue); border-top: 5px solid transparent; border-bottom: 5px solid transparent; }

  .col-title { font-size: 19px; font-weight: 500; color: var(--link-blue); }
  .col-art { border: 1px solid #cfcfcf; }
  .body-copy { font-size: 14px; line-height: 25px; color: var(--text); }
  .news-head { font-size: 15px; font-weight: 600; color: var(--text-dark); }
  .news-date { font-size: 14px; font-weight: 600; color: var(--text); }

  .footer-rule { left: 16px; top: 812px; width: 919px; height: 1px; background: var(--rule); }
  .footer-nav { left: 19px; top: 839px; display: flex; gap: 20px; font-size: 13px; letter-spacing: .4px; color: var(--text); }
  .copyright { right: 26px; top: 840px; font-size: 13px; letter-spacing: .4px; color: var(--text); }
</style>
</head>
<body>
<div class="sheet">
  <header>
    <div class="abs brand"><span class="brand-mark"></span><span class="brand-name">Torvel Capital</span></div>
    <div class="abs account"><span>LOGIN</span><span class="sep">|</span><span>SIGN UP</span></div>
    <nav class="abs main-nav">
      <a href="#">Home</a><span class="sep">|</span>
      <a href="#">About</a><span class="sep">|</span>
      <a href="#">Services</a><span class="sep">|</span>
      <a href="#">Current Engagements</a><span class="sep">|</span>
      <a href="#">Completed Transactions</a>
      <form class="search">
        <input type="text" placeholder="enter search term">
        <button type="button" aria-label="Search"><svg width="8" height="9" viewBox="0 0 8 9"><path d="M0 0 L8 4.5 L0 9Z" fill="#fff"/></svg></button>
      </form>
    </nav>
  </header>

  <section>
    <div class="abs hero-art" role="img" aria-label="Glass office tower seen from below against a pale sky"></div>
    <h1 class="abs hero-title">A bank of INVESTMENT</h1>
    <p class="abs hero-lede">One of the Leading Dallas-based Private Investment Banking Advisory Firm!</p>
    <a class="abs more" href="#" style="left:28px;top:299px">READ MORE</a>
    <div class="abs hero-dots"><i></i><i></i><i class="on"></i><i></i></div>

    <div class="abs services">
      <h2>Our Special Services</h2>
      <ul>
        <li>Buy-Side Acquistions</li>
        <li>Recapitalization &amp; Growth Capital</li>
        <li>Sell Side Transactions</li>
        <li>Current Engagements</li>
        <li>Completed Transactions</li>
        <li>Regulatory Complaince</li>
      </ul>
      <a class="more" href="#" style="display:block;margin-top:20px;padding-left:2px">VIEW MORE</a>
    </div>
  </section>

  <section>
    <h2 class="abs col-title" style="left:13px;top:471px">Our Company</h2>
    <div class="abs col-art" style="left:13px;top:521px;width:332px;height:137px;background:linear-gradient(90deg,#c9ccd0,#6b7480 50%,#b9bdc2)" role="img" aria-label="Team of five business professionals standing in an office"></div>
    <p class="abs body-copy" style="left:15px;top:669px;width:320px">Lorem Ipsum is simply dummy text of the printing and typesetting industry. Lorem Ipsum has been the industry's since the 1500s Ipsum has been.</p>
    <a class="abs more" href="#" style="left:15px;top:760px">READ MORE</a>

    <h2 class="abs col-title" style="left:372px;top:471px">Latest News</h2>
    <h3 class="abs news-head" style="left:372px;top:520px">Lorem Ipsum Dolor Sit amet and entering</h3>
    <p class="abs body-copy" style="left:372px;top:544px;width:305px">Lorem Ipsum is simply dummy text of the print-ing and typesetting industry.</p>
    <p class="abs news-date" style="left:372px;top:605px">02/07/14</p>
    <h3 class="abs news-head" style="left:372px;top:643px">Lorem Ipsum Dolor Sit amet and entering.</h3>
    <p class="abs body-copy" style="left:372px;top:667px;width:305px">Lorem Ipsum is simply dummy text of the print-ing and typesetting industry.</p>
    <p class="abs news-date" style="left:372px;top:723px">02/07/14</p>
    <a class="abs more" href="#" style="left:372px;top:760px">VIEW ALL</a>

    <h2 class="abs col-title" style="left:704px;top:472px">Our Global Network</h2>
    <div class="abs col-art" style="left:707px;top:520px;width:231px;height:137px;background:linear-gradient(90deg,#dfe8f1,#2a4a7a 40%,#1d3c6b 70%,#2f8fc9)" role="img" aria-label="World map with office locations, Asia/Pacific highlighted"></div>
    <p class="abs body-copy" style="left:707px;top:667px;width:230px">Lorem Ipsum is simply dummy text of the printing and typesetting industry.</p>
    <a class="abs more" href="#" style="left:705px;top:760px">READ MORE</a>
  </section>

  <footer>
    <div class="abs footer-rule"></div>
    <nav class="abs footer-nav"><span>Home</span><span>Terms &amp; Conditions</span><span>Contact Us</span></nav>
    <p class="abs copyright">© 2014 Torvel Capital. All Rights Reserved</p>
  </footer>
</div>
</body>
</html>
```